Counseling Practice Business Card

I need a professional looking business card incorporating my new logo that was just completed. Card needs to incorporate my name and title, description of my specialty, my address, my phone number, my fax number, my email and my website URL. I need to be able to choose design on/with different paper colors and textures.
I do not have a lot of business card ideas so I am open to anything but I want bold,sharp, clear card without additional designs other than my logo (see attached file info). I am open to different color backgrounds or paper colors including black. I do not like traditional brackets around area codes in phone number or dashes between numbers in phone number. Am open to other ways of presenting including periods between numbers as appropriate. I do not know enough to know what I like yet but I want card to coordinate and work together with my logo. My practice emphasizes natural mental health interventions so any use of color (with background paper color or the blue and green in my logo) that elicits nature is nice. In addition to black, any natural brown or wood looking background might be desirable also. Most of the offerings so far look very similar and boring.

Target Market(s)

Potential therapy clients and other professionals

Contact Information for Business Card

Card information:
Gerald M. Whitcombe, Ph.D.
Licensed Clinical Psychologist
Integrative Health Coach
4812 Marlowe Ridge Blvd SE
Suite 310
Duluth, GA 30096
(770) 415-2983 phone
(770) 581-4096 fax
drgeraldwhitcombe@quillmarsh.net
brightfernwellness.net

Font styles to use
Serif
Sans Serif
Other font styles liked:
• anything that you think looks crisp, clear and easily readable

Requirements
Must have
• Any color used should coordinate with my logo design (see attached files).
• Card should be printed horizontally so top and bottom are longest sides of rectangle.
• Background color or paper color should complement and highlight logo. Do not like a white background. black, grey, brown or any color my logo would blend well with.
Nice to have
• I would like designer to utilize color to highlight letters/name or phone-fax-web symbols.
• Bottom edge of card could be highlighted if appropriate to an idea.
Should not have
• I would NOT want the card to have a pure white background at all.
• No clear cards.
• Cards should be oriented with long sides on bottom and top, NOT sides. DO NOT LIKE THIS THIN TALL ORIENTATION.

```html
<!DOCTYPE html>
<html lang="en">
<head>
<meta charset="utf-8">
<title>Brightfern Wellness – Business Card</title>
<link rel="stylesheet" href="https://fonts.googleapis.com/css2?family=Roboto:wght@400;500;700&display=swap">
<style>
  :root {
    --stage: #2a2a2c;
    --card: #1f1f21;
    --card-edge: #2b2b2e;
    --ink: #f4f4f4;
    --accent: #1f7fcf;
    --mark-grey: #8d8d90;
  }
  * { margin: 0; padding: 0; box-sizing: border-box; }
  html, body {
    width: 1200px; height: 900px; overflow: hidden;
    background: var(--stage);
    font-family: "Roboto", Arial, sans-serif;
  }
  .canvas {
    position: relative; width: 1200px; height: 900px;
    display: flex; flex-direction: column; align-items: center; justify-content: center; gap: 40px;
  }
  .card {
    width: 700px; height: 400px;
    background: linear-gradient(135deg, var(--card-edge), var(--card) 60%);
    box-shadow: 0 10px 30px rgba(0,0,0,.45);
    position: relative;
  }
  .card-back { display: flex; align-items: center; justify-content: center; }
  .practice-name {
    font-family: "Roboto", Arial, sans-serif;
    font-weight: 500;
    letter-spacing: 1px;
    line-height: 1;
  }
  .card-back .practice-name { color: var(--mark-grey); font-size: 52px; }
  .card-front { display: flex; align-items: center; padding: 0 40px 0 46px; }
  .front-mark { width: 300px; display: flex; align-items: center; gap: 12px; }
  .front-mark .dot { width: 18px; height: 18px; border-radius: 50%; background: var(--accent); flex: none; }
  .front-mark .practice-name { color: var(--accent); font-size: 34px; }
  .divider { width: 3px; height: 230px; background: var(--ink); margin: 0 22px 0 8px; }
  .details { color: var(--ink); font-size: 17px; line-height: 1.3; }
  .person-name { color: var(--accent); font-weight: 700; font-size: 23px; margin-bottom: 4px; }
  .title { font-weight: 500; }
  .address { margin-top: 12px; font-weight: 500; }
  .contact { list-style: none; margin-top: 12px; }
  .contact li { display: flex; align-items: center; gap: 10px; }
  .contact svg { width: 13px; height: 13px; fill: none; stroke: var(--accent); stroke-width: 2; flex: none; }
  .web-name { color: var(--accent); }
</style>
</head>
<body>
<main class="canvas">
  <section class="card card-back">
    <span class="practice-name">Brightfern Wellness</span>
  </section>

  <section class="card card-front">
    <div class="front-mark">
      <span class="dot"></span>
      <span class="practice-name">Brightfern Wellness</span>
    </div>
    <div class="divider"></div>
    <div class="details">
      <p class="person-name">Gerald M. Whitcombe, Ph.D.</p>
      <p class="title">Licensed Clinical Psychologist</p>
      <p class="title">Integrative Health Coach</p>
      <p class="address">4812 Marlowe Ridge Blvd SE<br>Suite 310 Duluth, GA 30096</p>
      <ul class="contact">
        <li><svg viewBox="0 0 16 16"><path d="M4 1.5l2.5 3-1.5 1.8c.9 2 2.6 3.7 4.7 4.7l1.8-1.5 3 2.5-1.5 2.5C7.5 14 2 8.5 1.5 3z"/></svg>(770) 415-2983</li>
        <li><svg viewBox="0 0 16 16"><rect x="2" y="6" width="12" height="6"/><rect x="4.5" y="2" width="7" height="4"/><rect x="4.5" y="10" width="7" height="4"/></svg>(770) 581-4096</li>
        <li><svg viewBox="0 0 16 16"><rect x="1.5" y="3.5" width="13" height="9"/><path d="M1.5 3.5L8 9l6.5-5.5"/></svg>drgeraldwhitcombe@quillmarsh.net</li>
        <li><svg viewBox="0 0 16 16"><circle cx="8" cy="8" r="6.5"/><ellipse cx="8" cy="8" rx="3" ry="6.5"/><path d="M1.5 8h13"/></svg><span>www.<span class="web-name">brightfernwellness</span>.net</span></li>
      </ul>
    </div>
  </section>
</main>
</body>
</html>
```